IV Nutritional Clinic Web Design

We are working with Velqo. They are an IV Nutritional Clinic and in need of a new website design.
Some sites to use for inspiration:
https://brightpathcareco.com
https://www.ourzavrowellness.com
https://www.dewspringlounge.com
https://qvitalsurge.com
https://www.lumo-vital.com/pages/iv-therapy-west-hollywood
https://www.tqoncologyhub.com/cancer-care/iv-drips/
https://dripwellary.com
https://corvinahealthhub.com
Thank you for taking the time to consider designing a website for us. We are web developers based in Stockton, CA, USA. Most of our projects go through the same process. Understanding this process may help you win a project with us. We custom-code all of our websites in-house. We don’t have any requirements as to what tools you use for your design, but we prefer Figma files. For any design that we label as four-stars, we send it to the client for review. The client picks the final design they want us to use. Once we complete this process, we will continue to show additional clients all the four-star sites and purchase them later. Your designs will have multiple chances to sell. For better chances of success, we ask that you follow these guidelines.
IMAGES:
If you use any images or icons in the design, we ask that you have a link to the asset so we can purchase the image/icon. Most of the designs we submit do not have the customer’s images on them unless they have some great images. Be creative; show us the feeling you are trying to portray with your image choices. Use any royalty-free site you choose. We subscribe to Pixvane and mainly use their images, but we can purchase images outside of Pixvane.
PLEASE NOTE: we will not submit designs to clients with watermarks on the images.
FONTS:
We ask that you identify the fonts used in the design. This can be done in a message if you want. We typically use Google Fonts and Pixvane Fonts.
CONTENT:
We're always open to different content and ideas. We often submit designs with stock images so the client can see our vision. We typically take pictures after the website launch to use their images with our vision. Lorem Ipsum is fine for paragraphs, but we ask that you write the headers in correct English. We want to be able to show the vision and identify the sections of the website.
INSPIRATION:
We typically add a couple of links in the brief of websites we like to help you get started in your design.
REVISIONS:
We do not often ask for revisions of the designs unless we see something in the design that may not appeal to the client. If there are slight changes that we want to make, we do that in the development process.
FEEDBACK:
We rarely give feedback on designs during the design process. We are working on many website projects and do not have the time to provide feedback. We usually respond if your request is well thought out and asks specific questions, but a note asking “feedback, please” usually goes unanswered.

```html
<!DOCTYPE html>
<html lang="en">
<head>
<meta charset="utf-8">
<title>Velqo Hydration — IV Nutritional Clinic</title>
<link href="https://fonts.googleapis.com/css2?family=Fira+Sans:wght@400;500;600;700&family=Open+Sans:wght@400;600;700&display=swap" rel="stylesheet">
<style>
:root{
  --navy:#1a2456;
  --navy-deep:#141c47;
  --green:#7aa443;
  --field:#3b3878;
  --page:#f4f6f9;
  --text:#6b7080;
  --dark:#1e1f22;
  --white:#ffffff;
}
*{margin:0;padding:0;box-sizing:border-box}
html,body{width:1200px;height:4183px;overflow:hidden}
body{position:relative;background:var(--page);font-family:"Open Sans",sans-serif;color:var(--text)}
.abs{position:absolute}
.head{font-family:"Fira Sans",sans-serif;color:var(--navy);font-weight:600}
.label{font-family:"Open Sans",sans-serif;font-size:13px;color:var(--green);font-weight:600;text-decoration:underline;text-underline-offset:4px;text-transform:uppercase}
.center{left:0;width:1200px;text-align:center}

/* header */
.site-header{top:0;left:0;width:1200px;height:122px;background:var(--white)}
.brand{left:49px;top:30px;font-family:"Fira Sans",sans-serif;font-weight:700;font-size:42px;color:var(--navy);letter-spacing:2px}
.updates{left:222px;top:0;width:978px;height:54px;background:#f1f2f4;font-size:12px;line-height:54px;padding-left:66px}
.updates b{color:#e0642b;margin-right:6px}
.updates .dot{position:absolute;left:42px;top:21px;width:13px;height:11px;border:1.5px solid var(--green);border-radius:2px}
.nav{top:78px;font-family:"Fira Sans",sans-serif;font-size:11.5px;font-weight:600;color:var(--navy)}
.nav.active{color:var(--green)}
.phone-ring{left:966px;top:65px;width:49px;height:49px;border-radius:50%;background:#3b3d45}
.enq{left:1028px;top:68px;font-size:11px;font-weight:700;color:var(--green)}
.enq-num{left:1028px;top:88px;font-size:15px;font-weight:700;color:var(--navy)}

/* hero */
.hero{top:122px;left:0;width:1200px;height:710px;background:linear-gradient(100deg,#1c2a5e 0%,#2b3c70 40%,#5b6c8c 70%,#8fa0b3 100%)}
.hero-title{left:114px;top:185px;font-family:"Fira Sans",sans-serif;font-weight:600;font-size:41px;line-height:47px;color:var(--white)}
.hero-text{left:114px;top:300px;width:410px;font-size:18px;line-height:26px;color:var(--white);font-weight:600}
.btn-pill{left:114px;top:406px;width:144px;height:40px;border-radius:20px;background:var(--green);color:var(--white);font-size:12px;font-weight:700;text-align:center;line-height:40px}
.hero-wave{left:0;bottom:0;width:1200px;height:140px}

/* about */
.about-ring{left:97px;top:901px;width:447px;height:431px;border-radius:50%;background:#4a5088}
.about-photo{left:115px;top:906px;width:429px;height:426px;border-radius:50%;background:radial-gradient(circle at 55% 40%,#e9ecef 0%,#c7ccd3 55%,#8a93a3 100%)}
.about-badge{left:434px;top:1226px;width:102px;height:102px;border-radius:50%;background:var(--white);box-shadow:0 4px 14px rgba(0,0,0,.12)}
.about-title{left:617px;top:942px;font-size:42px;line-height:54px}
.about-sub{left:617px;top:1074px;font-family:"Fira Sans",sans-serif;font-size:23px;color:var(--navy);font-weight:500}
.about-text{left:617px;top:1116px;width:505px;font-size:13px;line-height:22px}
.btn-box{height:44px;background:var(--green);color:var(--white);font-family:"Fira Sans",sans-serif;font-weight:600;font-size:16px;line-height:44px;padding-left:16px}
.btn-box svg{position:absolute;right:14px;top:14px}

/* services */
.services{top:1392px;left:0;width:1200px;height:633px;background:var(--white)}
.sec-title{font-size:42px}
.card{top:212px;width:321px;height:345px;overflow:hidden}
.card-photo{width:100%;height:100%}
.card-bar{left:0;bottom:0;width:100%;height:48px;background:rgba(30,40,85,.82);color:var(--white);font-family:"Fira Sans",sans-serif;font-weight:600;font-size:19px;text-align:center;line-height:50px}
.card-icon{left:128px;bottom:24px;width:64px;height:64px;border-radius:50%;background:rgba(40,50,95,.85)}
.card-icon svg{position:absolute;left:19px;top:14px}
.card-mid{background:linear-gradient(180deg,#2a3466,#3a4375)}
.card-mid h3{position:absolute;top:172px;left:0;width:100%;text-align:center;font-family:"Fira Sans",sans-serif;font-weight:600;font-size:20px;color:var(--white)}
.card-mid p{position:absolute;top:212px;left:42px;width:237px;text-align:center;font-size:13.5px;line-height:21px;color:var(--white)}

/* help band */
.help{top:2025px;left:0;width:1200px;height:422px;background:linear-gradient(100deg,#1c2a5c 0%,#253567 55%,#2e3d6f 100%);overflow:hidden}
.help-circle{left:692px;top:64px;width:500px;height:500px;border-radius:50%;background:rgba(255,255,255,.08)}
.help-photo{left:731px;top:56px;width:454px;height:366px;background:linear-gradient(180deg,#dfe6ee 0%,#9fb3c8 60%,#5577a4 100%);opacity:.92}
.help-title{left:100px;top:76px;font-family:"Fira Sans",sans-serif;font-weight:600;font-size:50px;line-height:64px;color:var(--white)}
.help-text{left:100px;top:213px;font-size:23px;line-height:34px;color:var(--white)}

/* testimonials */
.review{top:2644px;width:318px;height:182px;background:var(--white);border-radius:6px;box-shadow:0 6px 18px rgba(20,30,70,.08);padding:40px 22px 0;font-size:16px;line-height:23px}
.review.featured{background:var(--green);color:var(--white)}
.review-tail{top:2826px;width:0;height:0;border-top:20px solid var(--green);border-right:20px solid transparent}
.avatar{top:2857px;width:55px;height:55px;border-radius:50%;background:linear-gradient(180deg,#e6e8ec,#b9bec8)}
.author{top:2858px;font-family:"Fira Sans",sans-serif;font-weight:600;font-size:15px;color:var(--navy)}
.author.alt{color:var(--green)}
.role{top:2882px;font-size:12px;color:#8a8f9c}
.dots{top:2958px;left:565px}
.dots span{display:inline-block;width:9px;height:9px;border-radius:50%;background:#bcd39c;margin-right:4px;vertical-align:middle}
.dots span.on{width:22px;border-radius:5px;background:var(--navy)}

/* contact */
.form-box{left:112px;top:3266px;width:484px;height:359px;background:var(--navy)}
.form-title{left:50px;top:24px;font-family:"Fira Sans",sans-serif;font-weight:600;font-size:25px;color:var(--white)}
.form-rule{left:226px;top:42px;width:45px;height:2px;background:var(--green)}
.field{background:var(--field);color:#e3e4ef;font-size:12px;padding-left:17px;line-height:36px}
.contact-photo{left:596px;top:3282px;width:484px;height:331px;background:linear-gradient(135deg,#eef2f6 0%,#cfd9e4 50%,#6f95c4 100%)}

/* footer */
.footer{top:3719px;left:0;width:1200px;height:464px;background:var(--dark);overflow:hidden}
.footer-wave{left:0;top:0;width:1200px;height:100px}
.footer-brand{left:146px;top:208px;font-family:"Fira Sans",sans-serif;font-weight:700;font-size:54px;color:var(--white);letter-spacing:3px}
.f-info{top:238px;font-size:14px;line-height:19px;color:#e6e6e6;white-space:nowrap}
.f-sep{top:228px;width:1px;height:52px;background:#55575c}
.f-line{left:257px;width:706px;height:1px;background:#55575c}
.f-nav{top:331px;font-size:14.5px;color:var(--white)}
.f-copy{left:146px;top:410px;font-size:12px;color:var(--white)}
.social{top:406px;width:26px;height:26px;border:1px solid #9a9ca0}
.social i{position:absolute;left:7px;top:7px;width:10px;height:10px;background:var(--white)}
</style>
</head>
<body>

<header class="abs site-header">
  <div class="abs brand">VELQO</div>
  <div class="abs updates"><span class="dot"></span><b>UPDATES:</b>Lorem ipsum dolor sit amet, consectetur adipiscing elit, sed do eiusmod tempor incididunt ut labore et dolore magna aliqua.</div>
  <span class="abs nav active" style="left:248px">HOME</span>
  <span class="abs nav" style="left:323px">ABOUT US</span>
  <span class="abs nav" style="left:416px">TREATMENTS</span>
  <span class="abs nav" style="left:523px">NEW PATIENTS</span>
  <span class="abs nav" style="left:641px">FEES</span>
  <span class="abs nav" style="left:700px">CONTACT US</span>
  <div class="abs phone-ring">
    <svg width="49" height="49" viewBox="0 0 49 49"><path d="M18 15c2 0 3 4 3 5s-2 2-2 3c1 3 4 6 7 7 1 0 2-2 3-2s5 1 5 3-2 4-4 4c-8 0-16-8-16-16 0-2 2-4 4-4z" fill="#fff"/></svg>
  </div>
  <span class="abs enq">ENQUIRIES</span>
  <span class="abs enq-num">+ 1-800-555-01-472</span>
</header>

<section class="abs hero">
  <div class="abs" role="img" aria-label="Clinician caring for a senior patient reclining in a treatment chair" style="left:0;top:0;width:1200px;height:710px"></div>
  <h1 class="abs hero-title">Vital Nutrients,<br>Amplified Wellness</h1>
  <p class="abs hero-text">Lorem ipsum dolor sit amet, consectetur adip iscing elit, sed do eiusmod tempor incididunt ut labore et dolore</p>
  <div class="abs btn-pill">READ MORE</div>
  <svg class="abs hero-wave" viewBox="0 0 1200 140" preserveAspectRatio="none">
    <path d="M0 140 L0 112 C260 40 520 30 760 98 C960 150 1100 96 1200 58 L1200 140 Z" fill="#f4f6f9"/>
    <path d="M0 108 C260 36 520 26 760 94 C960 146 1100 92 1200 54 L1200 72 C1100 112 960 166 760 118 C520 56 260 66 0 122 Z" fill="#7aa443"/>
  </svg>
</section>

<section>
  <div class="abs about-ring"></div>
  <div class="abs about-photo" role="img" aria-label="Smiling doctor with clipboard and medical team behind"></div>
  <div class="abs about-badge">
    <svg class="abs" style="left:26px;top:26px" width="50" height="50" viewBox="0 0 50 50">
      <g stroke="#7aa443" stroke-width="4" stroke-linecap="round">
        <line x1="25" y1="4" x2="25" y2="12"/><line x1="25" y1="38" x2="25" y2="46"/>
        <line x1="4" y1="25" x2="12" y2="25"/><line x1="38" y1="25" x2="46" y2="25"/>
        <line x1="10" y1="10" x2="15" y2="15"/><line x1="35" y1="35" x2="40" y2="40"/>
        <line x1="40" y1="10" x2="35" y2="15"/><line x1="10" y1="40" x2="15" y2="35"/>
      </g>
    </svg>
  </div>
  <span class="abs label" style="left:617px;top:909px">Who we are</span>
  <h2 class="abs head about-title">The team you can trust<br>to get the job done</h2>
  <h3 class="abs about-sub">Nourishment Without Limits</h3>
  <p class="abs about-text">Lorem ipsum dolor sit amet, consectetur adipiscing elit, sed do eiusmod tempor incididunt ut labore et dolore magna aliqua. Ut enim ad minim veniam, quis nos trud exercitation ullamco laboris nisi ut aliquip ex ea commodo consequat. Duis aute irure dolor in reprehenderit in voluptate velit esse cillum dolore eu fugiat nulla pariatur. Excepteur sint occaecat cupidatat non proident, sunt in culpa qui officia deserunt mollit anim id est laborum.</p>
  <div class="abs btn-box" style="left:619px;top:1275px;width:154px">Contact us
    <svg width="18" height="16" viewBox="0 0 18 16"><path d="M1 8h15M10 2l6 6-6 6" stroke="#fff" stroke-width="2" fill="none"/></svg>
  </div>
</section>

<section class="abs services">
  <div class="abs center" style="top:75px"><span class="label">Our services</span></div>
  <h2 class="abs head sec-title center" style="top:110px">Services We Offer</h2>

  <div class="abs card" style="left:93px">
    <div class="card-photo" role="img" aria-label="Smiling young girl at a clinic visit" style="background:linear-gradient(160deg,#8fa7bf 0%,#c9b8a8 55%,#9fb2c4 100%)"></div>
    <div class="abs card-icon"><svg width="26" height="26" viewBox="0 0 26 26"><path d="M13 3l9 7-3.5 11h-11L4 10z" stroke="#fff" stroke-width="2" fill="none"/></svg></div>
    <div class="abs card-bar">Performance Boosters</div>
  </div>

  <div class="abs card card-mid" style="left:438px">
    <svg class="abs" style="left:128px;top:98px" width="64" height="60" viewBox="0 0 64 60"><path d="M32 6l23 17-9 29H18L9 23z" stroke="#fff" stroke-width="3" fill="none"/><circle cx="32" cy="6" r="4" fill="#fff"/><circle cx="55" cy="23" r="4" fill="#fff"/><circle cx="46" cy="52" r="4" fill="#fff"/><circle cx="18" cy="52" r="4" fill="#fff"/><circle cx="9" cy="23" r="4" fill="#fff"/></svg>
    <h3>Hydration Therapy</h3>
    <p>Lorem ipsum dolor sit amet, conse ctetur adipiscing elit, sed do eius mod tempor incididunt ut labore et dolore magna aliqua.</p>
  </div>

  <div class="abs card" style="left:788px">
    <div class="card-photo" role="img" aria-label="Happy patient giving thumbs up with gloved clinician" style="background:linear-gradient(160deg,#e8eaee 0%,#d7c5b8 50%,#4a86c8 100%)"></div>
    <div class="abs card-icon"><svg width="26" height="26" viewBox="0 0 26 26"><path d="M13 3l9 7-3.5 11h-11L4 10z" stroke="#fff" stroke-width="2" fill="none"/></svg></div>
    <div class="abs card-bar">Detox Infusions</div>
  </div>
</section>

<section class="abs help">
  <div class="abs help-circle"></div>
  <div class="abs help-photo" role="img" aria-label="Doctor and nurse in masks reviewing a clipboard"></div>
  <h2 class="abs help-title">NEED HELP? WE'RE<br>AVAILABLE 24/7</h2>
  <p class="abs help-text">Call Us or submit a form below to speak with<br>an expert today for a free quote</p>
  <div class="abs btn-box" style="left:106px;top:313px;width:154px">Contact us
    <svg width="18" height="16" viewBox="0 0 18 16"><path d="M1 8h15M10 2l6 6-6 6" stroke="#fff" stroke-width="2" fill="none"/></svg>
  </div>
</section>

<section>
  <div class="abs center" style="top:2493px"><span class="label">Testimonials</span></div>
  <h2 class="abs head sec-title center" style="top:2528px">Clients' Reviews</h2>

  <div class="abs review" style="left:93px">Lorem ipsum dolor sit amet, consectetur adipiscing elit, sed do eiusmod tempor incididunt ut labore et dolore magna aliqua. Ut enim ad minim veniam.</div>
  <div class="abs review featured" style="left:437px">Lorem ipsum dolor sit amet, consectetur adipiscing elit, sed do eiusmod tempor incididunt ut labore et dolore magna aliqua. Ut enim ad minim veniam.</div>
  <div class="abs review" style="left:783px">Lorem ipsum dolor sit amet, consectetur adipiscing elit, sed do eiusmod tempor incididunt ut labore et dolore magna aliqua. Ut enim ad minim veniam.</div>

  <div class="abs review-tail" style="left:93px"></div>
  <div class="abs review-tail" style="left:437px"></div>
  <div class="abs review-tail" style="left:783px"></div>

  <div class="abs avatar" style="left:110px" role="img" aria-label="Reviewer portrait"></div>
  <span class="abs author" style="left:191px">Jhon Smith</span><span class="abs role" style="left:188px">Engineer</span>
  <div class="abs avatar" style="left:457px" role="img" aria-label="Reviewer portrait"></div>
  <span class="abs author alt" style="left:536px">Jhon Smith</span><span class="abs role" style="left:533px">Engineer</span>
  <div class="abs avatar" style="left:802px" role="img" aria-label="Reviewer portrait"></div>
  <span class="abs author" style="left:882px">Jhon Smith</span><span class="abs role" style="left:879px">Engineer</span>

  <div class="abs dots"><span class="on"></span><span></span><span></span><span></span></div>
</section>

<section>
  <div class="abs center" style="top:3095px"><span class="label">Contact us</span></div>
  <h2 class="abs head sec-title center" style="top:3130px">Get un Touch with Us</h2>

  <div class="abs contact-photo" role="img" aria-label="Smiling dental team in masks with a patient"></div>
  <form class="abs form-box">
    <div class="abs form-title">Get in touch</div>
    <div class="abs form-rule"></div>
    <div class="abs field" style="left:50px;top:76px;width:184px;height:36px">Your name*</div>
    <div class="abs field" style="left:253px;top:76px;width:181px;height:36px">Phone number...</div>
    <div class="abs field" style="left:50px;top:127px;width:384px;height:36px">Choose Service*
      <svg class="abs" style="right:16px;top:15px" width="10" height="6" viewBox="0 0 10 6"><path d="M1 1l4 4 4-4" stroke="#fff" stroke-width="1.5" fill="none"/></svg>
    </div>
    <div class="abs field" style="left:50px;top:177px;width:384px;height:98px;line-height:20px;padding-top:12px">Message...</div>
    <div class="abs" style="left:50px;top:289px;width:124px;height:37px;background:var(--green);color:#fff;font-size:11px;font-weight:700;line-height:37px;padding-left:34px">
      <svg class="abs" style="left:16px;top:13px" width="12" height="12" viewBox="0 0 12 12"><path d="M1 6l10-5-4 10-1.5-4z" stroke="#fff" stroke-width="1.2" fill="none"/></svg>Book Online</div>
  </form>
</section>

<footer class="abs footer">
  <div class="abs" role="img" aria-label="Dim clinic interior backdrop" style="left:0;top:0;width:1200px;height:464px;background:linear-gradient(180deg,#3a3d44 0%,#1e1f22 55%)"></div>
  <svg class="abs footer-wave" viewBox="0 0 1200 100" preserveAspectRatio="none">
    <path d="M0 0 H1200 V22 C1080 50 900 86 700 76 C480 64 260 10 0 78 Z" fill="#f4f6f9"/>
    <path d="M0 72 C260 4 480 58 700 70 C900 80 1080 44 1200 16 L1200 26 C1080 58 900 96 700 86 C480 74 260 22 0 90 Z" fill="#7aa443"/>
  </svg>
  <div class="abs footer-brand">VELQO</div>

  <div class="abs f-sep" style="left:414px"></div>
  <svg class="abs" style="left:433px;top:240px" width="30" height="30" viewBox="0 0 30 30"><circle cx="15" cy="15" r="12" stroke="#ddd" stroke-width="1.5" fill="none"/><ellipse cx="15" cy="15" rx="5" ry="12" stroke="#ddd" stroke-width="1.5" fill="none"/><line x1="3" y1="15" x2="27" y2="15" stroke="#ddd" stroke-width="1.5"/></svg>
  <p class="abs f-info" style="left:469px">48, Orchard Row, Suite 2<br>Lakeview, State ZQ 604219</p>
  <div class="abs f-sep" style="left:666px"></div>
  <svg class="abs" style="left:688px;top:238px" width="30" height="34" viewBox="0 0 30 34"><rect x="4" y="3" width="16" height="28" rx="2" stroke="#ddd" stroke-width="1.5" fill="none"/><line x1="10" y1="27" x2="14" y2="27" stroke="#ddd" stroke-width="1.5"/><path d="M24 12c2 3 2 7 0 10" stroke="#ddd" stroke-width="1.5" fill="none"/></svg>
  <p class="abs f-info" style="left:726px">PHONE<br>(555) 014 7720</p>
  <div class="abs f-sep" style="left:845px"></div>
  <svg class="abs" style="left:864px;top:242px" width="30" height="26" viewBox="0 0 30 26"><rect x="2" y="4" width="26" height="18" stroke="#ddd" stroke-width="1.5" fill="none"/><path d="M2 4l13 10 13-10" stroke="#ddd" stroke-width="1.5" fill="none"/></svg>
  <p class="abs f-info" style="left:905px">EMAIL<br>care@velqo.example</p>

  <div class="abs f-line" style="top:313px"></div>
  <span class="abs f-nav" style="left:276px">HOME</span>
  <span class="abs f-nav" style="left:370px">SERVICES</span>
  <span class="abs f-nav" style="left:476px">ABOUT US</span>
  <span class="abs f-nav" style="left:594px">TESTIMONIALS</span>
  <span class="abs f-nav" style="left:745px">BLOG</span>
  <span class="abs f-nav" style="left:836px">CONTACT US</span>
  <div class="abs f-line" style="top:369px"></div>

  <span class="abs f-copy">VELQO HYDRATION</span>
  <div class="abs social" style="left:934px" aria-label="Social link"><i></i></div>
  <div class="abs social" style="left:966px" aria-label="Social link"><i></i></div>
  <div class="abs social" style="left:1000px" aria-label="Social link"><i></i></div>
  <div class="abs social" style="left:1034px" aria-label="Social link"><i></i></div>
</footer>

</body>
</html>
```